Federal Government Proposal Development Consulting company needs a website designed and coded

I am looking for someone to design (using an existing logo, color palette, and text fonts) and code a wordpress-based website for a Proposal Development consulting company. I have full copy for all site pages and suggestions for images/ graphics and a few example design templates to go from.

One note, from a color perspective - I included a mockup of a business card to highlight a color scheme that I tend to like - if you look at the back of the business card, the blend of the grey, blue, with the neon green highlight as a separator really seems to pop. Just a thought as you are designing the page.

I would like to see 2-3 potential design layouts, and I will select one to move forward with. Then, I would like the site to be coded for WordPress (I can provide a login to my wordpress site). I would like 1 opportunity to review the coded site and make any final tweaks.

```html
<!DOCTYPE html>
<html lang="en">
<head>
<meta charset="utf-8">
<title>The Clear Quill Consulting LLC</title>
<link href="https://fonts.googleapis.com/css2?family=Fondamento&family=Montserrat:wght@400;500;600;700&display=swap" rel="stylesheet">
<style>
:root{
  --blue:#0b46c8;
  --blue-deep:#0a3aa8;
  --navy:#07122b;
  --green:#19efb3;
  --grey:#f4f4f4;
  --ink:#1c1c1c;
  --muted:#444;
  --white:#fff;
  --black:#0b0b0b;
}
*{box-sizing:border-box;margin:0;padding:0}
html,body{width:1200px;height:4955px;overflow:hidden}
body{position:relative;font-family:"Montserrat",sans-serif;color:var(--ink);background:var(--white)}
.abs{position:absolute}
.script{font-family:"Fondamento",cursive;font-weight:400}
.btn{position:absolute;display:flex;align-items:center;justify-content:center;background:var(--green);color:#06302a;font-weight:700;font-size:14px;border-radius:6px;letter-spacing:.3px}
.photo{position:absolute}

/* header + hero */
.hero{position:absolute;left:0;top:0;width:1200px;height:760px;background:radial-gradient(ellipse at 75% 45%,#4a5a78 0%,#1b2a48 35%,#07122b 75%);overflow:hidden}
.hero::before{content:"";position:absolute;left:0;top:0;width:1200px;height:5px;background:var(--green)}
.hero-oval{position:absolute;left:10px;top:245px;width:720px;height:380px;border-radius:50%;background:rgba(5,12,60,.7);border:3px solid #000}
.brand{position:absolute;left:108px;top:28px;color:#c9cdd6;line-height:1}
.brand .name{font-size:36px}
.brand .sub{font-size:16px;margin-left:42px;display:block;margin-top:2px}
.nav{position:absolute;top:38px;left:0;width:1200px;height:20px;color:var(--white);font-size:14px}
.nav span{position:absolute}
.nav-line{position:absolute;left:0;top:86px;width:1200px;height:1px;background:rgba(255,255,255,.55)}
.hero h1{position:absolute;left:108px;top:352px;font-size:78px;color:var(--white);line-height:1}
.hero p{position:absolute;left:108px;top:450px;font-size:15px;color:var(--white);line-height:28px}
.logo-dot{position:absolute;left:562px;top:728px;width:76px;height:76px;border-radius:50%;background:var(--white);box-shadow:0 2px 8px rgba(0,0,0,.2)}

/* what we do */
.what{position:absolute;left:0;top:760px;width:1200px;height:813px;background:var(--grey)}
.sec-title{font-family:"Fondamento",cursive;font-size:38px;color:var(--ink);position:absolute}
.what .copy{position:absolute;left:112px;top:198px;width:492px;font-size:14px;line-height:29.6px;color:var(--muted)}
.what .lead{position:absolute;left:661px;top:180px;width:410px;font-size:19.5px;font-weight:600;line-height:39.4px;color:var(--ink)}
.tile{position:absolute;top:1394px;width:311px;height:343px}
.tile-cap{background:var(--blue);display:flex;flex-direction:column;align-items:center;justify-content:center;color:var(--white)}
.tile-cap h3{font-family:"Fondamento",cursive;font-weight:400;font-size:31px;line-height:36px;text-align:center}
.tile-cap a{color:var(--green);font-size:13px;font-weight:600;margin-top:6px;text-decoration:underline}

/* who */
.who .copy{position:absolute;left:112px;top:1965px;width:575px;font-size:14px;line-height:29.6px;color:var(--muted)}
.circle-photo{position:absolute;left:735px;top:1846px;width:354px;height:354px;border-radius:50%;background:linear-gradient(180deg,#9fb1c4 0%,#d8dee6 45%,#5a78a8 100%)}

/* blue band */
.band{position:absolute;left:0;top:2308px;width:1200px;height:730px;background:linear-gradient(100deg,#0b46c8 0%,#1650d4 55%,#0b46c8 100%)}
.band-title{position:absolute;width:1200px;text-align:center;font-family:"Fondamento",cursive;font-size:38px;color:var(--white)}
.avatar{position:absolute;border-radius:50%;background:linear-gradient(160deg,#c7b4a6,#6a5348);border:3px solid var(--white)}
.dot{position:absolute;border-radius:50%}
.testi-name{position:absolute;width:1200px;text-align:center;top:2554px;color:var(--white);font-weight:700;font-size:18px}
.testi-role{position:absolute;width:1200px;text-align:center;top:2582px;color:var(--white);font-size:14px}
.stars{position:absolute;left:557px;top:2613px}
.quote{position:absolute;left:290px;top:2655px;width:620px;text-align:center;font-size:14px;line-height:26px;color:var(--white)}
.qmark{position:absolute;font-family:Georgia,serif;font-size:130px;color:rgba(255,255,255,.35);line-height:1}
.round-btn{position:absolute;width:34px;height:34px;border-radius:50%;display:flex;align-items:center;justify-content:center}

/* services */
.svc{position:absolute;background:var(--blue);border:6px solid var(--white);box-shadow:0 6px 18px rgba(0,0,0,.18)}
.svc .img{position:absolute;left:0;top:0;right:0}
.svc .label{position:absolute;left:0;right:0;bottom:0;display:flex;align-items:center;justify-content:center;text-align:center;color:var(--white);font-family:"Fondamento",cursive;font-size:17px;line-height:20px;background:var(--blue)}
.svc-center{text-align:center;color:var(--white)}
.svc-center h4{font-family:"Fondamento",cursive;font-weight:400;font-size:22px;margin-top:105px}
.svc-center p{font-size:12px;line-height:25.6px;padding:0 24px;margin-top:12px}
.svc-center a{display:block;color:var(--green);font-family:"Fondamento",cursive;font-size:14px;margin-top:16px;text-decoration:underline}
.chev{position:absolute}

/* expertise */
.sme{position:absolute;top:3510px;width:408px;height:321px}
.sme h5{position:absolute;left:23px;top:200px;font-family:"Fondamento",cursive;font-weight:400;font-size:24px;color:var(--white)}
.sme p{position:absolute;left:23px;top:240px;width:370px;font-size:13.5px;line-height:25px;color:var(--white)}
.sme .go{position:absolute;right:22px;bottom:-20px;width:54px;height:54px;border-radius:50%;background:var(--green);border:4px solid var(--white);display:flex;align-items:center;justify-content:center}

/* contact */
.contact{position:absolute;left:0;top:3938px;width:1200px;height:604px;background:var(--grey)}
.field{position:absolute;background:var(--white);font-size:15px;color:#444;padding:18px 22px;box-shadow:0 3px 10px rgba(0,0,0,.05)}
.submit{position:absolute;left:513px;top:4405px;width:166px;height:60px;background:var(--blue);color:var(--white);border-radius:8px;font-weight:700;font-size:16px;display:flex;align-items:center;justify-content:center}

/* footer */
.footer{position:absolute;left:0;top:4542px;width:1200px;height:413px;background:var(--black);color:var(--white)}
.foot-brand{position:absolute;left:120px;top:88px;color:#c9cdd6;line-height:1}
.foot-brand .name{font-size:54px}
.foot-brand .sub{display:block;font-size:25px;margin:6px 0 0 70px}
.foot-head{position:absolute;top:86px;font-family:"Fondamento",cursive;font-size:23px}
.foot-list{position:absolute;font-size:14px;line-height:30px;list-style:none}
.foot-rule{position:absolute;left:112px;top:319px;width:976px;height:1px;background:#333}
.copyright{position:absolute;top:358px;width:1200px;text-align:center;font-size:14px}
.copyright b{color:var(--green);font-weight:500}
</style>
</head>
<body>

<header class="hero">
  <div class="photo" role="img" aria-label="Business team reviewing data on a tablet in a server room" style="left:0;top:0;width:1200px;height:760px;background:linear-gradient(90deg,rgba(7,18,43,.9) 0%,rgba(7,18,43,.3) 50%,rgba(20,30,55,.2) 100%)"></div>
  <div class="hero-oval"></div>
  <div class="brand script"><span class="name">The Clear Quill</span><span class="sub">Consulting LLC</span></div>
  <nav class="nav">
    <span style="left:496px">Home</span>
    <span style="left:573px">Work with Us</span>
    <span style="left:700px">Work for Us</span>
    <span style="left:817px">About Us</span>
    <span style="left:917px">Contact</span>
    <svg style="position:absolute;left:1072px;top:0" width="18" height="18" viewBox="0 0 18 18"><circle cx="7" cy="7" r="5" fill="none" stroke="#fff" stroke-width="2"/><line x1="11" y1="11" x2="16" y2="16" stroke="#fff" stroke-width="2.5"/></svg>
  </nav>
  <div class="nav-line"></div>
  <h1 class="script">Generate Success</h1>
  <p>Fuel Innovation in Proposal Excellence with The Clear Quill!<br>Click here to explore our services.</p>
  <div class="btn script" style="left:110px;top:523px;width:136px;height:46px;font-family:'Fondamento',cursive;font-weight:400;font-size:15px">Get Started</div>
</header>

<section class="what">
  <h2 class="sec-title" style="left:112px;top:130px">What We Do</h2>
  <p class="copy">The Clear Quill, specializes in advancing an organization through a comprehensive suite of services designed to modernize the proposal development process. From innovative Capture Management strategies that pinpoint lucrative opportunities, meticulous Proposal Development services that transform concepts into effective narratives, and cutting-edge Generative AI techniques that create domain-aware content accelerating proposal draft development, we are your dedicated partner in securing success. With a unique fusion of technical expertise and exceptional writing capabilities, we surpass industry standards and set new benchmarks for excellence.</p>
  <p class="lead">Discover a dynamic approach to proposal consulting that goes beyond conventional boundaries—choose The Clear Quill for solutions that Enhance the quality of your work, Elevate your corporate advantage, and Expand your industry presence.</p>
  <div class="btn" style="left:659px;top:490px;width:152px;height:52px">LEARN MORE</div>
</section>
<div class="logo-dot"></div>

<div class="tile photo" role="img" aria-label="Team gathered around a laptop at a meeting table" style="left:127px;background:linear-gradient(160deg,#e7e7e7 0%,#9a9a9a 55%,#4a4a4a 100%)"></div>
<div class="tile tile-cap" style="left:454px"><h3>Capture<br>Management</h3><a>LEARN MORE</a></div>
<div class="tile photo" role="img" aria-label="Colleagues planning at a wall of sticky notes" style="left:781px;background:linear-gradient(150deg,#d9dde0 0%,#9ca3a8 50%,#5e6468 100%)"></div>

<section class="who">
  <h2 class="sec-title" style="left:112px;top:1898px">Who We Are</h2>
  <p class="copy">Lorem ipsum dolor sit amet, consectetur adipiscing elit, sed do eiusmod tempor incididunt ut labore et dolore magna aliqua. Quis ipsum suspendisse ultrices gravida. Risus commodo viverra maecenas accumsan lacus vel facilisis.</p>
  <div class="btn" style="left:114px;top:2070px;width:132px;height:46px">ABOUT US</div>
  <div class="circle-photo" role="img" aria-label="Presenter showing charts on a screen in a boardroom"></div>
</section>

<section class="band">
  <div class="photo" role="img" aria-label="Smiling professional in glasses, blue tinted background" style="left:640px;top:60px;width:560px;height:500px;background:radial-gradient(ellipse at 40% 40%,rgba(40,80,170,.7) 0%,rgba(11,70,200,0) 70%)"></div>
</section>
<h2 class="band-title" style="top:2372px">Testimonials</h2>
<div class="avatar" role="img" aria-label="Client portrait" style="left:559px;top:2449px;width:90px;height:90px"></div>
<div class="avatar" role="img" aria-label="Client portrait" style="left:145px;top:2508px;width:48px;height:48px;border-width:2px"></div>
<div class="avatar" role="img" aria-label="Client portrait" style="left:959px;top:2425px;width:48px;height:48px;border-width:2px"></div>
<div class="dot" style="left:147px;top:2424px;width:7px;height:7px;background:var(--green)"></div>
<div class="dot" style="left:333px;top:2528px;width:9px;height:9px;background:#f5b400"></div>
<div class="dot" style="left:915px;top:2378px;width:9px;height:9px;background:#f5a000"></div>
<div class="dot" style="left:825px;top:2560px;width:8px;height:8px;background:#b82bd8"></div>
<div class="dot" style="left:1026px;top:2725px;width:9px;height:9px;background:var(--green)"></div>
<div class="round-btn" style="left:214px;top:2556px;background:var(--green)"><svg width="10" height="10" viewBox="0 0 10 10"><path d="M6.5 1.5 3 5l3.5 3.5" fill="none" stroke="#06302a" stroke-width="1.6"/></svg></div>
<div class="round-btn" style="left:967px;top:2556px;border:1px solid rgba(255,255,255,.6)"><svg width="10" height="10" viewBox="0 0 10 10"><path d="M3.5 1.5 7 5 3.5 8.5" fill="none" stroke="#fff" stroke-width="1.6"/></svg></div>
<div class="testi-name">Morgan Ellery</div>
<div class="testi-role">Lorem Ipsum</div>
<svg class="stars" width="100" height="18" viewBox="0 0 100 18">
  <g fill="#f5b400">
    <path id="st" d="M9 1l2.3 5 5.4.5-4.1 3.6 1.2 5.3L9 12.6 4.2 15.4l1.2-5.3L1.3 6.5l5.4-.5z"/>
    <use href="#st" x="20"/><use href="#st" x="40"/><use href="#st" x="60"/><use href="#st" x="80"/>
  </g>
</svg>
<div class="qmark" style="left:254px;top:2570px">“</div>
<div class="qmark" style="left:890px;top:2718px">”</div>
<p class="quote">Lorem ipsum dolor sit amet, consectetur adipiscing elit, sed do eiusmod tempor incididunt ut labore et dolore magna aliqua. Quis ipsum suspendisse ultrices gravida. Risus commodo viverra maecenas accumsan lacus vel facilisis.</p>

<h2 class="band-title" style="top:2804px">Our Services</h2>
<div class="svc" style="left:137px;top:2932px;width:273px;height:360px">
  <div class="img photo" role="img" aria-label="Robotic hand reaching toward a human hand" style="height:290px;background:linear-gradient(135deg,#0e2236 0%,#2f4a62 45%,#8a5048 60%,#c9a996 100%)"></div>
  <div class="label" style="height:58px">Generative AI</div>
</div>
<div class="svc svc-center" style="left:442px;top:2900px;width:321px;height:423px">
  <h4>Technical Solutioning</h4>
  <p>Lorem ipsum dolor sit amet, consectetur adipiscing elit, sed do eiusmod tempor incididunt ut labore et dolore magna aliqua. Quis ipsum suspendisse ultrices gravida. Risus commodo viverra maecenas accumsan lacus vel facilisis.</p>
  <a>Learn More</a>
</div>
<div class="svc" style="left:796px;top:2932px;width:273px;height:360px">
  <div class="img photo" role="img" aria-label="Business partners meeting over laptops" style="height:290px;background:linear-gradient(160deg,#e9e6e2 0%,#b3aba4 50%,#6f5c50 100%)"></div>
  <div class="label" style="height:58px">Price to Win/ Competitive<br>Intelligence</div>
</div>
<svg class="chev" style="left:54px;top:3142px" width="16" height="24" viewBox="0 0 16 24"><path d="M12 2 3 12l9 10" fill="none" stroke="#111" stroke-width="2.5"/></svg>
<svg class="chev" style="left:1134px;top:3142px" width="16" height="24" viewBox="0 0 16 24"><path d="M4 2l9 10-9 10" fill="none" stroke="#111" stroke-width="2.5"/></svg>

<h2 class="band-title" style="top:3408px;color:var(--ink)">Subject Matter Expertise</h2>
<div class="sme">
</div>
<div class="sme photo" role="img" aria-label="Glowing circuit board with AI graphic" style="left:167px;background:linear-gradient(160deg,#0b2a48 0%,#12507a 50%,#061a30 100%)">
  <h5>Generative AI</h5>
  <p>Lorem ipsum dolor sit amet, consectetur adipiscing elit, sed do eiusmod tempor incididunt</p>
  <div class="go"><svg width="16" height="14" viewBox="0 0 16 14"><path d="M1 7h13M9 2l5 5-5 5" fill="none" stroke="#06302a" stroke-width="2"/></svg></div>
</div>
<div class="sme photo" role="img" aria-label="Engineers working in a data center" style="left:623px;background:linear-gradient(110deg,#0a1d3a 0%,#1e3f66 45%,#3d5f86 70%,#0f2444 100%)">
  <h5>Software/ Hardware Engineering</h5>
  <p>Lorem ipsum dolor sit amet, consectetur adipiscing elit, sed do eiusmod tempor incididunt</p>
  <div class="go"><svg width="16" height="14" viewBox="0 0 16 14"><path d="M1 7h13M9 2l5 5-5 5" fill="none" stroke="#06302a" stroke-width="2"/></svg></div>
</div>
<svg class="chev" style="left:77px;top:3661px" width="16" height="24" viewBox="0 0 16 24"><path d="M12 2 3 12l9 10" fill="none" stroke="#111" stroke-width="2.5"/></svg>
<svg class="chev" style="left:1094px;top:3661px" width="16" height="24" viewBox="0 0 16 24"><path d="M4 2l9 10-9 10" fill="none" stroke="#111" stroke-width="2.5"/></svg>

<section class="contact">
  <h2 class="band-title" style="top:55px;color:var(--ink)">Contact Us</h2>
</section>
<div class="field" style="left:148px;top:4088px;width:439px;height:58px">First Name</div>
<div class="field" style="left:604px;top:4088px;width:438px;height:58px">Last Name</div>
<div class="field" style="left:148px;top:4169px;width:439px;height:58px">Email</div>
<div class="field" style="left:604px;top:4169px;width:438px;height:58px">Phone</div>
<div class="field" style="left:148px;top:4246px;width:894px;height:119px">Message</div>
<div class="submit">SUBMIT</div>

<footer class="footer">
  <div class="foot-brand script"><span class="name">The Clear Quill</span><span class="sub">Consulting LLC</span></div>
  <h6 class="foot-head" style="left:635px">Quick Links</h6>
  <ul class="foot-list" style="left:632px;top:112px">
    <li>«&nbsp; Home</li><li>«&nbsp; Work with Us</li><li>«&nbsp; Work for Us</li><li>«&nbsp; About Us</li><li>«&nbsp; Contact</li>
  </ul>
  <h6 class="foot-head" style="left:831px">Contact Us</h6>
  <ul class="foot-list" style="left:833px;top:112px">
    <li><svg width="14" height="11" viewBox="0 0 14 11" style="margin-right:10px"><rect width="14" height="11" rx="1" fill="#fff"/><path d="M1 1.5 7 6l6-4.5" fill="none" stroke="#0b0b0b" stroke-width="1.3"/></svg>info@ClearQuillGroup.com</li>
    <li><svg width="13" height="13" viewBox="0 0 13 13" style="margin-right:11px"><path d="M3 .5 5 3.5 3.6 5c.8 1.8 2.5 3.5 4.4 4.4L9.5 8l3 2-1 2.5C6 12.5.5 7 .5 1.5z" fill="#fff"/></svg>(410) 555-0148</li>
  </ul>
  <div class="foot-rule"></div>
  <p class="copyright">©Copyrights 2023 &nbsp;<b>The Clear Quill</b> | &nbsp; All Rights Reserved</p>
</footer>

</body>
</html>
```